App Design - Career Prep Pal

We require an App Design for our new App called 'Hiring Helper'. This app is essentially an assistant to help Users prepare for job interviews, to help them get hired. <br/><br/>Users who download the App can view common Questions and Answers, save their favourite responses and also view common Interview Tips. <br/><br/>The vision for our App is for Users who are preparing for an interview (1 week before, 1 day before, even 1 hour before), are able to download, view and educate themselves on common questions and responses, and then be confident to land the job. <br/><br/>Our team has developed wireframes to help highlight what each screen should do and include. Please see attached document, which also highlights key requirements for the experience. Feel free to add/remove/edit what you see on these wireframes. Our preference is that you use Adobe XD please.<br/><br/>In terms of design guidelines, we want the experience to be simple, intuitive and 'memorable' to help Users to remember the questions/responses when they are in the interview. <br/><br/>The final design should communicate 'neat and clean professionalism'; we like the design of: jobvista net au<br/><br/>Thank you for reading! Good luck !

Target Market(s)

Professional job seekers

Font styles to use
Sans Serif

Colors

Designer to choose colors to be used in the design.

Requirements
Must have
• Please see my PixelGuild_UX file that I have uploaded
Nice to have
• Could you also please include some ideas on how we can incorporate Advertising into the app screens

```html
<!DOCTYPE html>
<html lang="en">
<head>
<meta charset="utf-8">
<title>Hiring Helper – Interview Tips</title>
<link rel="stylesheet" href="https://fonts.googleapis.com/css2?family=Poppins:wght@300;400;600;700&display=swap">
<style>
  :root {
    --page-bg: #ffffff;
    --screen-bg: #f7f9f8;
    --green-light: #8cff00;
    --green-deep: #14ff00;
    --accent: #7dff00;
    --card-border: #86ff2a;
    --card-bg: #ffffff;
    --ink: #1b1b1b;
    --ink-soft: #2a2a2a;
    --white: #ffffff;
  }
  * { box-sizing: border-box; margin: 0; padding: 0; }
  html, body {
    width: 1200px; height: 1200px; overflow: hidden;
    background: var(--page-bg);
    font-family: "Poppins", sans-serif;
  }
  .canvas { position: relative; width: 1200px; height: 1200px; }
  .app-screen {
    position: absolute; left: 319px; top: 68px;
    width: 562px; height: 1064px;
    background: var(--screen-bg);
    border-radius: 60px;
    overflow: hidden;
    box-shadow: 0 6px 18px rgba(0,0,0,0.12);
  }
  .app-header {
    position: absolute; left: 0; top: 0; width: 100%; height: 150px;
    background: linear-gradient(90deg, var(--green-light), var(--green-deep));
  }
  .status-time {
    position: absolute; left: 44px; top: 10px;
    font-size: 17px; font-weight: 700; color: var(--ink);
  }
  .status-icons { position: absolute; right: 52px; top: 12px; }
  .back-button { position: absolute; left: 24px; top: 70px; }
  .app-title {
    position: absolute; left: 0; right: 0; top: 68px; text-align: center;
    padding-left: 20px;
    font-size: 36px; font-weight: 700; color: var(--white);
  }
  .section-title {
    position: absolute; left: 0; right: 0; top: 192px; text-align: center;
    font-size: 25px; font-weight: 600; color: var(--ink);
  }
  .section-subtitle {
    position: absolute; left: 0; right: 0; top: 234px; text-align: center;
    font-size: 19px; font-weight: 400; color: var(--ink-soft);
  }
  .tip-card {
    position: absolute; left: 35px; width: 489px;
    background: var(--card-bg);
    border: 1.5px solid var(--card-border);
    border-radius: 14px;
    box-shadow: 0 6px 10px rgba(0,0,0,0.14);
  }
  .tip-card--before { top: 392px; height: 196px; }
  .tip-card--during { top: 605px; height: 194px; }
  .tip-card--after  { top: 828px; height: 196px; }
  .tip-card svg { position: absolute; left: 50%; transform: translateX(-50%); }
  .tip-label {
    position: absolute; left: 0; right: 0; bottom: 20px; text-align: center;
    font-size: 19px; font-weight: 400; color: var(--ink);
  }
  .view-all {
    position: absolute; left: 126px; top: 1049px; width: 331px; height: 65px;
    background: var(--accent); border-radius: 14px;
    color: var(--white); font-size: 30px; font-weight: 300;
    display: flex; align-items: center; justify-content: center;
  }
</style>
</head>
<body>
<div class="canvas">
  <div class="app-screen" style="top:18px;">
    <header class="app-header">
      <span class="status-time">05:30 AM</span>
      <svg class="status-icons" width="80" height="22" viewBox="0 0 80 22" aria-hidden="true">
        <rect x="0" y="13" width="3" height="6" fill="#1b1b1b"/>
        <rect x="5" y="10" width="3" height="9" fill="#1b1b1b"/>
        <rect x="10" y="7" width="3" height="12" fill="#1b1b1b"/>
        <rect x="15" y="4" width="3" height="15" fill="#1b1b1b"/>
        <rect x="28" y="3" width="44" height="17" rx="8.5" fill="none" stroke="#1b1b1b" stroke-width="2"/>
        <rect x="73" y="8" width="4" height="7" rx="1.5" fill="#1b1b1b"/>
        <text x="50" y="16.5" text-anchor="middle" font-family="Poppins, sans-serif" font-size="12" font-weight="700" fill="#1b1b1b">50</text>
      </svg>
      <svg class="back-button" width="48" height="48" viewBox="0 0 48 48" aria-label="Back">
        <path d="M40 24H10M24 10 10 24l14 14" fill="none" stroke="#ffffff" stroke-width="6" stroke-linecap="round" stroke-linejoin="round"/>
      </svg>
      <h1 class="app-title">Hiring Helper</h1>
    </header>

    <h2 class="section-title">Interview Tips</h2>
    <p class="section-subtitle">Select your interview tips category</p>

    <div class="tip-card tip-card--before" style="top:323px;">
      <svg style="top:38px" width="96" height="96" viewBox="0 0 96 96" aria-hidden="true">
        <path d="M86 48H18M48 14 14 48l34 34" fill="none" stroke="#7dff00" stroke-width="12" stroke-linecap="round" stroke-linejoin="round"/>
      </svg>
      <p class="tip-label">Tips for befor interview</p>
    </div>

    <div class="tip-card tip-card--during" style="top:536px;">
      <svg style="top:22px" width="180" height="124" viewBox="0 0 180 124" aria-hidden="true">
        <circle cx="90" cy="62" r="50" fill="none" stroke="#7dff00" stroke-width="10"/>
        <path d="M6 48 40 80 62 52" fill="none" stroke="#7dff00" stroke-width="10" stroke-linecap="round" stroke-linejoin="round"/>
        <path d="M174 78 140 46 118 72" fill="none" stroke="#7dff00" stroke-width="10" stroke-linecap="round" stroke-linejoin="round"/>
      </svg>
      <p class="tip-label">Tips for during the interview</p>
    </div>

    <div class="tip-card tip-card--after" style="top:759px;">
      <svg style="top:38px" width="96" height="96" viewBox="0 0 96 96" aria-hidden="true">
        <path d="M10 48H78M48 14l34 34-34 34" fill="none" stroke="#7dff00" stroke-width="12" stroke-linecap="round" stroke-linejoin="round"/>
      </svg>
      <p class="tip-label">Tips for after the interfiew</p>
    </div>

    <div class="view-all" style="top:985px;">View All</div>
  </div>
</div>
</body>
</html>
```